Copperbend Blazeworks Website Design

I am looking for a website design ( Home page and inner template page ) in a .psd format. The home page needs to have a large hero image what will function as a "slider", and have some highlight graphical areas/links to the following links "Public & Municipal Events", "Corporate Events", "Special Events". The main navigation needs to have the following nav links "gallery", "home", "about", "services" and "contact". Unfortunately the client does not have any nice hi-rez images ( this is a company that specializes is large fireworks displays ) so please use stock photography sample images from snapvaultpics since we have an account there an can purchase the photos if our client wants to use them. Our current full time graphic artist has been with us for a long time so we are looking at artflockhub as a way to add a fresh approach to design and possibly find someone we can work with regularly. Here is a few designs that in the way we display them for our clients for approval. As you can see there are a couple that don't have their own images so they are utilizing the before mentioned snapvaultpics samples. On the plus side we did manage to get their logo in a .ai format. We have our team for handling the conversion from design to html.

http://reedfoxbuildstudio.com/dev/

```html
<!DOCTYPE html>
<html lang="en">
<head>
<meta charset="utf-8">
<title>Copperbend Blazeworks</title>
<link href="https://fonts.googleapis.com/css2?family=Lora:wght@400;700&display=swap" rel="stylesheet">
<style>
:root{
  --blue:#3a8dc8;
  --blue-light:#4c9ad3;
  --ink:#1d1d1d;
  --body:#4a4a4a;
  --grey-btn:#8f8f8f;
  --white:#ffffff;
  --night:#0a0c2e;
}
*{margin:0;padding:0;box-sizing:border-box}
html,body{width:1200px;height:2528px;overflow:hidden}
body{position:relative;font-family:'Lora',serif;background:var(--white);color:var(--ink)}
.hero{position:absolute;left:0;top:0;width:1200px;height:600px;
  background:radial-gradient(ellipse at 38% 55%,#3c4fd0 0%,#2a2a9a 25%,transparent 55%),
  radial-gradient(ellipse at 68% 48%,#a040b8 0%,#5a2a9a 28%,transparent 55%),
  linear-gradient(180deg,#05061a 0%,#0c0e3a 60%,#1a1f7a 100%)}
.brand-badge{position:absolute;left:144px;top:-10px;width:221px;height:172px;background:var(--white);
  border:4px solid var(--blue);border-top:none;border-radius:0 0 110px 110px;display:flex;align-items:center;justify-content:center;text-align:center}
.brand-badge span{font-size:24px;line-height:1.15;color:var(--ink);padding:0 18px}
.main-nav{position:absolute;top:50px;right:146px;display:flex;gap:35px}
.main-nav a{color:var(--white);text-decoration:none;font-weight:700;font-size:17px;padding-bottom:6px}
.main-nav a.active{border-bottom:3px solid var(--blue-light)}
.slider-dots{position:absolute;left:1130px;top:405px;display:flex;flex-direction:column;gap:9px}
.slider-dots i{display:block;width:7px;height:7px;border-radius:50%;background:var(--white)}
.slider-dots i.on{background:var(--blue-light)}
.title-band{position:absolute;left:0;top:600px;width:1200px;height:110px;background:var(--blue);opacity:.97}
.title-band h1{position:absolute;left:143px;top:18px;font-size:56px;font-weight:700;color:var(--white)}
.btn{display:inline-block;background:var(--grey-btn);color:var(--white);font-family:'Lora',serif;font-weight:700;border-radius:30px;text-align:center;text-decoration:none}
.get-started{position:absolute;left:841px;top:627px;width:214px;height:56px;line-height:56px;font-size:20px}
.section-title{position:absolute;left:0;width:1200px;text-align:center;font-size:56px;font-weight:700;color:var(--ink)}
.events{position:absolute;left:143px;top:942px;display:flex;gap:86px}
.event{width:249px}
.event h3{font-size:16px;font-weight:700;margin-bottom:22px;white-space:nowrap}
.event p{font-size:13px;line-height:22.5px;color:var(--body)}
.event a{display:inline-block;margin-top:18px;font-size:16px;font-weight:700;color:var(--blue)}
.gallery{position:absolute;left:144px;top:1410px;display:grid;grid-template-columns:repeat(4,221px);grid-auto-rows:194px;gap:10px 9px}
.gallery div{border:1px solid #fff}
.load-more{position:absolute;left:492px;top:2067px;width:215px;height:57px;line-height:57px;font-size:20px}
.footer{position:absolute;left:0;top:2202px;width:1200px;height:326px;background:var(--blue);color:var(--white)}
.footer-brand{position:absolute;left:144px;top:150px;font-size:26px}
.footer h4{position:absolute;top:66px;font-size:21px;font-weight:400}
.contact{position:absolute;left:424px;top:116px;font-size:14px;line-height:24px}
.contact li{list-style:none;display:flex;gap:10px;margin-bottom:14px}
.contact svg{flex:none;margin-top:4px}
.newsletter p{position:absolute;left:744px;top:118px;font-size:14px}
.signup{position:absolute;left:745px;top:153px;width:309px;height:48px;border:2px solid var(--white);border-radius:26px;background:var(--white)}
.signup span{position:absolute;left:26px;top:14px;font-size:13px;color:#999}
.signup b{position:absolute;right:3px;top:3px;width:104px;height:38px;line-height:38px;border-radius:20px;background:var(--grey-btn);text-align:center;font-size:16px}
.copyright{position:absolute;left:145px;top:264px;font-size:14px}
.social{position:absolute;left:884px;top:256px;display:flex;gap:9px}
.social i{display:block;width:36px;height:36px;border:2px solid var(--white);border-radius:50%}
</style>
</head>
<body>
<header>
  <div class="hero" role="img" aria-label="Night sky filled with blue and purple firework bursts over a crowd"></div>
  <div class="brand-badge"><span>Copperbend Blazeworks</span></div>
  <nav class="main-nav">
    <a class="active" href="#">Home</a><a href="#">About</a><a href="#">Services</a><a href="#">Gallery</a><a href="#">Contact</a>
  </nav>
  <div class="slider-dots"><i></i><i class="on"></i><i></i><i></i></div>
  <div class="title-band"><h1>Copperbend Blazeworks</h1></div>
  <a class="btn get-started" href="#">GET STARETD</a>
</header>

<main>
  <h2 class="section-title" style="top:798px">Latest Events</h2>
  <section class="events">
    <article class="event"><h3>PUBLIC &amp; MUNICIPAL EVENTS</h3>
      <p>Lorem ipsum dolor sit ameonsectetur adipiscing elit, sed do eiusmod tempor incididunt ut labore et dolore magna aliq ipsum suspendisse ultrices gravida.<br>&nbsp;Risus commodo viverra maecenas accumsan lacus vel facilisis.</p>
      <a href="#">Learn more</a></article>
    <article class="event"><h3>CORPORATE EVENTS"</h3>
      <p>Lorem ipsum dolor sit ameonsectetur adipiscing elit, sed do eiusmod tempor incididunt ut labore et dolore magna aliq ipsum suspendisse ultrices gravida.<br>&nbsp;Risus commodo viverra maecenas accumsan lacus vel facilisis.</p>
      <a href="#">Learn more</a></article>
    <article class="event"><h3>SPECIAL EVENTS</h3>
      <p>Lorem ipsum dolor sit ameonsectetur adipiscing elit, sed do eiusmod tempor incididunt ut labore et dolore magna aliq ipsum suspendisse ultrices gravida.<br>&nbsp;Risus commodo viverra maecenas accumsan lacus vel facilisis.</p>
      <a href="#">Learn more</a></article>
  </section>

  <h2 class="section-title" style="top:1287px">Our Gallery</h2>
  <section class="gallery">
    <div role="img" aria-label="Pink and violet fireworks" style="background:linear-gradient(160deg,#3a1a6a,#8a2a8a 50%,#1a1040)"></div>
    <div role="img" aria-label="Single red firework over a monument" style="background:linear-gradient(180deg,#0a1a4a,#a03a6a 45%,#0a0e2a)"></div>
    <div role="img" aria-label="Fireworks over a city skyline" style="background:linear-gradient(180deg,#1a1030,#c05a3a 60%,#2a1a4a)"></div>
    <div role="img" aria-label="People watching fireworks at sunset" style="background:linear-gradient(180deg,#2a3050,#5a5a7a 55%,#d07a3a)"></div>
    <div role="img" aria-label="Colourful dotted firework bursts" style="background:linear-gradient(150deg,#3a1050,#2a6a7a 50%,#1a0a30)"></div>
    <div role="img" aria-label="Fireworks reflected on water" style="background:linear-gradient(180deg,#0a1030,#5a5a8a 50%,#c07a3a)"></div>
    <div role="img" aria-label="Crowd silhouettes under fireworks" style="background:linear-gradient(180deg,#1a1010,#6a3a30 55%,#0a0808)"></div>
    <div role="img" aria-label="Gold firework burst" style="background:linear-gradient(180deg,#0a1a20,#5a4a2a 50%,#081018)"></div>
    <div role="img" aria-label="Crowd under blue fireworks" style="background:linear-gradient(160deg,#1a3a8a,#3a4ab0 50%,#0a0e2a)"></div>
    <div role="img" aria-label="Blue and magenta firework trails" style="background:linear-gradient(150deg,#1a2a8a,#8a3ab0 55%,#1a0a4a)"></div>
    <div role="img" aria-label="Sparkler with glowing bokeh" style="background:radial-gradient(circle at 35% 60%,#e0a040,#4a2a20 40%,#1a1a2a)"></div>
    <div role="img" aria-label="Red, white and blue fireworks" style="background:linear-gradient(160deg,#0a1a6a,#8a2040 55%,#0a0e3a)"></div>
  </section>
  <a class="btn load-more" href="#">LOAD MORE</a>
</main>

<footer class="footer">
  <div class="footer-brand">Copperbend Blazeworks</div>
  <h4 style="left:424px">CONTACT INFO</h4>
  <ul class="contact">
    <li><svg width="14" height="18" viewBox="0 0 14 18"><path d="M7 0a7 7 0 0 0-7 7c0 5 7 11 7 11s7-6 7-11a7 7 0 0 0-7-7zm0 10a3 3 0 1 1 0-6 3 3 0 0 1 0 6z" fill="#fff"/></svg><span>122,Lorem ipsum dolor sit amet<br>consectetur adipieiusmod</span></li>
    <li><svg width="16" height="16" viewBox="0 0 16 16"><path d="M3.5 0l3 3.5-2 2a10 10 0 0 0 6 6l2-2 3.5 3-2.5 3.5C6 15 1 10 0 2.5z" fill="#fff"/></svg><span>Phone : 1 8888 888 8888</span></li>
  </ul>
  <h4 style="left:744px">SIGN UP NEWSLETTER</h4>
  <div class="newsletter"><p>Lorem ipsum dolor sit ametconsectetur</p></div>
  <div class="signup"><span>Enter Email</span><b>SIGN UP</b></div>
  <p class="copyright">Copyright © 2021 Copperbend Blazeworks.Al rights Reserved &nbsp;| &nbsp;Privacy &nbsp;| &nbsp;Terms and Use</p>
  <div class="social"><i></i><i></i><i></i><i></i></div>
</footer>
</body>
</html>
```